American cannabis tech company business card design

Pavrel.com is seeking a modern, professional, and brand-aligned business card that represents our company and its core values: Mission, Story, Values, and Impact. As an innovative cannabis company, we want a business card that is not only visually appealing but also serves as a representation of who we are and what we stand for.

Project Scope: Design a double-sided business card that integrates our brand identity and core values. Incorporate our key brand elements, ensuring a sleek and contemporary aesthetic. Visually reflect our core values (Mission, Story, Values, Impact) in a way that is engaging yet professional.

Target Market(s)

Vendors, third parties,

Contact Information for Business Card

Contact details (name, title, email, phone, website, etc.)

Font styles to use
Other font styles liked:
• Caslon, Centra

Colors

Designer to choose colors to be used in the design.

Requirements
Must have
• Pavrel.com logo and branding A creative yet clean way to integrate our core values (Mission, Story, Values, Impact) Modern typography and a well-structured layout
Nice to have
• forest green, grey, white, black
Should not have
• references to marijuana, leafs, plants, or related product

```html
<!DOCTYPE html>
<html lang="en">
<head>
<meta charset="utf-8">
<title>Pavrel.com Business Card</title>
<link rel="stylesheet" href="https://fonts.googleapis.com/css2?family=Montserrat:wght@400;500&family=Playfair+Display:wght@700;900&display=swap">
<style>
  :root {
    --forest: #1b3320;
    --paper: #ffffff;
    --cream: #fbf8f2;
    --backdrop: #1c1c1c;
  }
  * { margin: 0; padding: 0; box-sizing: border-box; }
  html, body { width: 1200px; height: 1059px; overflow: hidden; background: var(--backdrop); }
  .canvas { position: relative; width: 1200px; height: 1059px; }
  .card { position: absolute; border-radius: 18px; overflow: hidden; }
  .card-front { left: 253px; top: 89px; width: 691px; height: 396px; background: var(--paper); }
  .card-back { left: 253px; top: 546px; width: 695px; height: 395px; background: var(--forest); }
  .wave { position: absolute; inset: 0; width: 100%; height: 100%; }
  .wordmark {
    position: absolute;
    font-family: "Playfair Display", serif;
    font-weight: 900;
    letter-spacing: 1px;
    line-height: 1;
    white-space: nowrap;
  }
  .card-front .wordmark { right: 30px; top: 32px; font-size: 92px; color: var(--forest); }
  .card-back .wordmark { left: 0; right: 0; top: 122px; text-align: center; font-size: 134px; color: var(--cream); }
  .core-values {
    position: absolute; left: 0; right: 0; top: 300px;
    display: flex; justify-content: center; align-items: center; gap: 14px;
    list-style: none;
    font-family: "Montserrat", sans-serif; font-weight: 500; font-size: 13px;
    letter-spacing: 4px; text-transform: uppercase; color: var(--cream);
  }
  .core-values li + li::before {
    content: ""; display: inline-block; width: 5px; height: 5px; border-radius: 50%;
    background: var(--cream); margin-right: 14px; vertical-align: middle; position: relative; top: -2px;
  }
  .holder { position: absolute; left: 34px; top: 188px; color: var(--paper); }
  .holder-name { font-family: "Playfair Display", serif; font-weight: 700; font-size: 23px; line-height: 1; }
  .holder-title { font-family: "Playfair Display", serif; font-weight: 700; font-size: 12px; letter-spacing: 0.6px; margin-top: 6px; }
  .address {
    position: absolute; left: 31px; top: 246px;
    font-family: "Montserrat", sans-serif; font-size: 15px; line-height: 18px; color: var(--paper);
  }
  .contact-list { position: absolute; left: 34px; top: 301px; list-style: none; }
  .contact-list li {
    display: flex; align-items: center; gap: 9px; height: 25.5px;
    font-family: "Montserrat", sans-serif; font-size: 15px; color: var(--paper);
  }
  .contact-list svg { width: 15px; height: 15px; flex: none; }
</style>
</head>
<body>
<div class="canvas">
  <section class="card card-front">
    <svg class="wave" viewBox="0 0 1176 672" preserveAspectRatio="none" aria-hidden="true">
      <path fill="var(--forest)" d="M0,228 C180,160 380,200 560,320 C700,415 790,440 880,435 C1000,430 1120,360 1176,245 V672 H0 Z"/>
      <path fill="none" stroke="var(--paper)" stroke-width="8" d="M0,290 C200,220 420,250 560,350 C720,470 900,530 1040,512 C1110,500 1150,430 1176,372"/>
      <path fill="none" stroke="var(--paper)" stroke-width="5" d="M480,300 C650,410 850,505 1020,500 C1100,497 1150,425 1176,385"/>
    </svg>
    <div class="wordmark">PAVREL</div>
    <div class="holder">
      <div class="holder-name">Dana Whitfield</div>
      <div class="holder-title">Owner</div>
    </div>
    <div class="address">418 Linden Ave, #112<br>Fairmont, OH 431105</div>
    <ul class="contact-list">
      <li>
        <svg viewBox="0 0 24 24" aria-hidden="true"><path fill="var(--paper)" d="M6.6 10.8a15.2 15.2 0 0 0 6.6 6.6l2.2-2.2a1 1 0 0 1 1-.25 11.4 11.4 0 0 0 3.6.57 1 1 0 0 1 1 1V20a1 1 0 0 1-1 1A17 17 0 0 1 3 4a1 1 0 0 1 1-1h3.5a1 1 0 0 1 1 1c0 1.250.2 2.45.57 3.57a1 1 0 0 1-.25 1Z"/></svg>
        555-318-0427
      </li>
      <li>
        <svg viewBox="0 0 24 24" aria-hidden="true"><path fill="var(--paper)" d="M2 5h20v14H2Z"/><path fill="none" stroke="var(--forest)" stroke-width="2" d="M2 6l10 7 10-7"/></svg>
        info@pavrel.com
      </li>
      <li>
        <svg viewBox="0 0 24 24" aria-hidden="true"><circle cx="12" cy="12" r="10" fill="var(--paper)"/><path fill="none" stroke="var(--forest)" stroke-width="1.6" d="M2 12h20M12 2c3 3 3 17 0 20M12 2c-3 3-3 17 0 20"/></svg>
        www.pavrel.com
      </li>
    </ul>
  </section>
  <section class="card card-back">
    <div class="wordmark">PAVREL</div>
    <ul class="core-values">
      <li>Mission</li>
      <li>Story</li>
      <li>Values</li>
      <li>Impact</li>
    </ul>
  </section>
</div>
</body>
</html>
```